Business Card Design

The Kestrel Lodge Inn is the most centrally located motel in Grafton.
We are the only family owned motel in Grafton.
Our colour scheme is blue, whiteand black.

I have uploaded a photo of our new rooms and the logo for you to use Thanks. Looking good

Industry/Entity Type

Motel

Contact Information for Business Card

The Kestrel Lodge Inn
Gareth & Lorna Pelling
Owner/Operators
14-16 Wexbury Lane, Grafton NSW 2460
Ph: 02 6617 3904
Email: thekestrellodgeinn@mailvista.example
reception@kestrellodgeinn.example.au
www.kestrellodgeinn.example.au

Colors
0392cd
0455a3

```html
<!DOCTYPE html>
<html lang="en">
<head>
<meta charset="utf-8">
<title>The Kestrel Lodge Inn – Business Card</title>
<link href="https://fonts.googleapis.com/css2?family=Exo+2:wght@400;500;700&display=swap" rel="stylesheet">
<style>
  :root {
    --backdrop: #1e1e20;
    --card: #ffffff;
    --brand-blue: #0455a3;
    --accent-blue: #0392cd;
    --ink: #2b2b2b;
    --rule: #555555;
  }
  * { box-sizing: border-box; margin: 0; padding: 0; }
  html, body {
    width: 1200px; height: 754px; overflow: hidden;
    background: var(--backdrop);
    font-family: "Exo 2", sans-serif;
    color: var(--ink);
  }
  .stage {
    position: relative; width: 1200px; height: 754px;
    display: flex; align-items: center; justify-content: center; gap: 40px;
  }
  .card {
    position: relative; width: 540px; height: 310px;
    background: var(--card);
  }
  .brand {
    display: flex; align-items: center; gap: 12px;
    color: var(--brand-blue); font-weight: 700;
    text-transform: uppercase; letter-spacing: 1px; line-height: 1.05;
  }
  .brand-dot { flex: none; border-radius: 50%; background: var(--accent-blue); }

  /* front */
  .card-front .brand { position: absolute; left: 30px; bottom: 34px; font-size: 22px; width: 190px; }
  .card-front .brand-dot { width: 22px; height: 22px; }
  .person { position: absolute; left: 250px; top: 46px; }
  .person-name { font-size: 17px; font-weight: 500; letter-spacing: 1.5px; text-transform: uppercase; }
  .person-role { font-size: 10px; letter-spacing: 1px; margin-top: 2px; text-transform: uppercase; }
  .contact-list { position: absolute; left: 250px; top: 104px; list-style: none; }
  .contact-list li, .address {
    display: flex; align-items: center; gap: 7px;
    font-size: 11.5px; letter-spacing: 0.3px; white-space: nowrap;
  }
  .contact-list li { margin-bottom: 8px; }
  .icon { width: 14px; height: 14px; flex: none; }
  .rule { position: absolute; left: 250px; right: 30px; top: 222px; border-top: 1px solid var(--rule); }
  .address { position: absolute; left: 250px; top: 240px; }

  /* back */
  .card-back { display: flex; align-items: center; justify-content: center; }
  .card-back .brand { font-size: 30px; width: 270px; }
  .card-back .brand-dot { width: 30px; height: 30px; }
</style>
</head>
<body>
<main class="stage">
  <section class="card card-front" aria-label="Business card front">
    <div class="brand"><span class="brand-dot"></span><span>The Kestrel Lodge Inn</span></div>
    <div class="person">
      <p class="person-name">Gareth &amp; Lorna Pelling</p>
      <p class="person-role">Owner/Operators</p>
    </div>
    <ul class="contact-list">
      <li>
        <svg class="icon" viewBox="0 0 14 14"><circle cx="7" cy="7" r="7" fill="#2b2b2b"/><path d="M4.6 3.6l1.3 1.3-.7 1a4.5 4.5 0 0 0 2.9 2.9l1-.7 1.3 1.3-.9 1C7 10.2 3.8 7 3.6 4.5z" fill="#fff"/></svg>
        02 6617 3904
      </li>
      <li>
        <svg class="icon" viewBox="0 0 14 14"><circle cx="7" cy="7" r="7" fill="#2b2b2b"/><rect x="3.5" y="4.6" width="7" height="4.8" fill="#fff"/><path d="M3.5 4.6L7 7.4l3.5-2.8" stroke="#2b2b2b" stroke-width=".8" fill="none"/></svg>
        thekestrellodgeinn@mailvista.example
      </li>
      <li>
        <svg class="icon" viewBox="0 0 14 14"><circle cx="7" cy="7" r="7" fill="#2b2b2b"/><rect x="3.5" y="4.6" width="7" height="4.8" fill="#fff"/><path d="M3.5 4.6L7 7.4l3.5-2.8" stroke="#2b2b2b" stroke-width=".8" fill="none"/></svg>
        reception@kestrellodgeinn.example.au
      </li>
      <li>
        <svg class="icon" viewBox="0 0 14 14"><circle cx="7" cy="7" r="7" fill="#2b2b2b"/><g stroke="#fff" stroke-width=".8" fill="none"><circle cx="7" cy="7" r="3.8"/><ellipse cx="7" cy="7" rx="1.6" ry="3.8"/><path d="M3.2 7h7.6"/></g></svg>
        www.kestrellodgeinn.example.au
      </li>
    </ul>
    <div class="rule"></div>
    <p class="address">
      <svg class="icon" viewBox="0 0 14 14"><circle cx="7" cy="7" r="7" fill="#2b2b2b"/><path d="M7 3a2.6 2.6 0 0 0-2.6 2.6C4.4 7.6 7 11 7 11s2.6-3.4 2.6-5.4A2.6 2.6 0 0 0 7 3z" fill="#fff"/><circle cx="7" cy="5.6" r="1" fill="#2b2b2b"/></svg>
      14-16 Wexbury Lane, Grafton NSW 2460
    </p>
  </section>
  <section class="card card-back" aria-label="Business card back">
    <div class="brand"><span class="brand-dot"></span><span>The Kestrel Lodge Inn</span></div>
  </section>
</main>
</body>
</html>
```